Veltrona Pocket Folder

Create a new pocket folder
An Overview / Background of the Business & Services
We would like a new folder to use when making formal presentations
* The Target Market / Audience you are trying to reach
The target audience are commercial businesses that we are selling group insurance products to
* Design Specifics; any preferences or ideas for Style, Colour, Imagery, etc
We wanted to use the Houston, Texas skyline and create something that was simple, yet modern.
* Do you have an existing website or Facebook page were designers can learn more about your company?
Yes, http://www.veltronagroup.example and we are on Linked-In.
Updates
Project Deadline Extended Reason: We have many people who have to agree. We need to get an answer on the form of the ready art we will receive when we select a designer .Thank you. Added Thursday, April 27, 2017
Industry/Entity Type
Business
Look and feel
Each slider illustrates characteristics of the customer's brand and the style your logo design should communicate.

```html
<!DOCTYPE html>
<html lang="en">
<head>
<meta charset="utf-8">
<title>Veltrona Pocket Folder</title>
<link href="https://fonts.googleapis.com/css2?family=Source+Sans+3:wght@400;600;700&display=swap" rel="stylesheet">
<style>
  :root {
    --backdrop: #e4e4e4;
    --folder-gray: #6b6b70;
    --cover-white: #fbfbfb;
    --brand-blue: #1a8fd6;
    --brand-blue-deep: #0f78c2;
    --brand-blue-light: #2aa7e0;
    --skyline-gray: #d3d5d8;
    --skyline-pale: #e7ebef;
    --logo-gray: #67676b;
    --ink-light: #ffffff;
    --flap-text: #c9c9cc;
  }
  html, body {
    margin: 0;
    padding: 0;
    width: 1200px;
    height: 979px;
    overflow: hidden;
    background: var(--backdrop);
  }
  .folder-layout {
    display: block;
    width: 1200px;
    height: 979px;
    font-family: "Source Sans 3", Arial, sans-serif;
  }
  .flap, .pocket { fill: var(--folder-gray); }
  .cover { fill: var(--cover-white); }
  .wave-gray { fill: var(--folder-gray); }
  .wave-white { fill: var(--ink-light); }
  .wave-blue { fill: url(#blueBand); }
  .slit { stroke: var(--ink-light); stroke-width: 1.2; }
  .flap-url {
    fill: var(--flap-text);
    font-size: 8px;
    letter-spacing: 1.6px;
  }
  .brand-mark { fill: var(--brand-blue); }
  .brand-name {
    fill: var(--logo-gray);
    font-size: 42px;
    font-weight: 700;
  }
  .faint-mark { fill: #eef1f4; }
  .contact {
    fill: var(--ink-light);
    font-size: 8.5px;
  }
  .contact-company { font-weight: 700; }
  .contact-icon { fill: var(--ink-light); }
</style>
</head>
<body>
<svg class="folder-layout" viewBox="0 0 1177 960" preserveAspectRatio="none" xmlns="http://www.w3.org/2000/svg">
  <defs>
    <linearGradient id="blueBand" x1="0" y1="0" x2="1" y2="0">
      <stop offset="0" stop-color="var(--brand-blue-deep)"/>
      <stop offset="0.6" stop-color="var(--brand-blue-light)"/>
      <stop offset="1" stop-color="var(--brand-blue-deep)"/>
    </linearGradient>
    <linearGradient id="skylineTone" x1="0" y1="0" x2="0" y2="1">
      <stop offset="0" stop-color="var(--skyline-pale)"/>
      <stop offset="0.5" stop-color="var(--skyline-gray)"/>
      <stop offset="1" stop-color="var(--skyline-pale)"/>
    </linearGradient>
  </defs>

  <!-- Side flaps -->
  <path class="flap flap-left" d="M100,116 L135,116 L135,663 L100,663 L100,472 A12,12 0 0 0 100,448 Z"/>
  <path class="flap flap-right" d="M1017,116 L1052,116 L1052,448 A12,12 0 0 0 1052,472 L1052,663 L1017,663 Z"/>
  <text class="flap-url" transform="translate(121,350) rotate(-90)">www.veltronagroup.example</text>
  <text class="flap-url" transform="translate(1031,215) rotate(90)">www.veltronagroup.example</text>

  <!-- Pockets -->
  <path class="pocket pocket-left" d="M165,667 L573,667 L545,840 Q540,873 510,873 L165,873 Z"/>
  <path class="pocket pocket-right" d="M578,667 L985,667 L985,873 L640,873 Q610,873 605,840 Z"/>
  <g class="card-slits">
    <line class="slit" x1="711" y1="754" x2="739" y2="727"/>
    <line class="slit" x1="845" y1="727" x2="873" y2="754"/>
    <line class="slit" x1="711" y1="794" x2="739" y2="821"/>
    <line class="slit" x1="845" y1="821" x2="873" y2="794"/>
  </g>

  <!-- Cover panels -->
  <rect class="cover" x="135" y="114" width="882" height="553"/>

  <rect class="faint-mark" x="272" y="198" width="156" height="152" rx="16"/>

  <rect x="160" y="405" width="855" height="235" fill="url(#skylineTone)" opacity="0.85"
        role="img" aria-label="Houston, Texas city skyline silhouette in soft grays"/>

  <g class="brand-lockup">
    <rect class="brand-mark" x="656" y="259" width="52" height="52" rx="6"/>
    <text class="brand-name" x="718" y="301">Veltrona</text>
  </g>

  <!-- Wave band -->
  <path class="wave-gray" d="M135,505 C250,468 400,520 600,580 S900,662 1017,612 L1017,667 L135,667 Z"/>
  <path class="wave-white" d="M135,517 C250,488 400,526 600,586 S880,658 1017,620 L1017,667 L135,667 Z"/>
  <path class="wave-blue" d="M135,527 C250,498 400,531 600,592 S870,660 1017,628 L1017,667 L135,667 Z"/>

  <!-- Contact block -->
  <g class="contact">
    <text class="contact-company" x="160" y="621">Veltrona Agency LLC</text>
    <text x="160" y="634">2450 North Calder Way, Suite 310</text>
    <text x="160" y="646">Houston, Texas, 77001</text>

    <text x="531" y="621" text-anchor="end">555-014-2290</text>
    <text x="531" y="634" text-anchor="end">info@veltronagroup.example</text>
    <text x="531" y="647" text-anchor="end">veltronagroup.example</text>
  </g>
  <g class="contact-icons">
    <path class="contact-icon" d="M537,614 q1,-1 2,0 l1.5,2 q0.5,1 -0.5,1.5 q1,2.5 3,3.5 q0.5,-1 1.5,-0.5 l2,1.5 q1,1 0,2 q-2,1.5 -5,-1 q-3,-3 -4.5,-6 q-0.5,-2 0,-3 Z"/>
    <rect class="contact-icon" x="537" y="628" width="8" height="6"/>
    <path d="M537,628 L541,631.5 L545,628" stroke="var(--brand-blue)" stroke-width="0.8" fill="none"/>
    <circle cx="541" cy="644" r="4" fill="none" stroke="var(--ink-light)" stroke-width="1"/>
    <line x1="537" y1="644" x2="545" y2="644" stroke="var(--ink-light)" stroke-width="0.7"/>
    <ellipse cx="541" cy="644" rx="1.8" ry="4" fill="none" stroke="var(--ink-light)" stroke-width="0.7"/>
  </g>
</svg>
</body>
</html>
```